Bramblewick Co. Wordpress Design Project

Need a redesign of this site: http://www.thebramblewickco.example/. Client wants to highlight before and after images of refinished furniture in some way that really showcases their work. Client deals with refurbishing low, middle and high end patio furniture and wants to appeal across the board. However, their bread and butter is in high end furniture refinishing. The home page should highlight everything found on their current home page including same navigation. Please show a dropdown under Residential. Use a combination of blue, white, yellow and maybe orange colors.
Updates

Reason: Client is slow to give any feedback.

Industry/Entity Type

Residential

Requirements
Must have
• Include a mini contact form on the home page. Phone number prominently displayed. Dropdown under Residential.
Nice to have
• You may feel free to use different colors in the logo in order to make it work with the design better.

```html
<!DOCTYPE html>
<html lang="en">
<head>
<meta charset="utf-8">
<title>The Bramblewick Company – Patio Furniture Repair</title>
<link rel="stylesheet" href="https://fonts.googleapis.com/css2?family=PT+Sans:wght@400;700&display=swap">
<style>
:root{
  --orange-mid:#fea10a;
  --orange-deep:#f99a00;
  --bar-grey:#4a5663;
  --phone-grey:#2f5f93;
  --nav-blue:#2f74bd;
  --nav-blue-dark:#1d4f87;
  --nav-divider-dark:#17416f;
  --nav-divider-light:#4f8dcf;
  --heading-gold:#b97a0e;
  --hero-blue:#1f5a96;
  --text:#3a3a3a;
  --line:#e2e2e2;
  --footer-link:#8a1d0a;
  --button-blue:#2f74bd;
  --button-blue-dark:#1d4f87;
  --field-border:#c9d3de;
}
*{box-sizing:border-box;margin:0;padding:0}
html,body{width:1200px;height:1116px;overflow:hidden}
body{position:relative;background:#fff;font-family:"PT Sans",Arial,sans-serif;color:var(--text)}
.abs{position:absolute}

.site-header{left:0;top:0;width:1200px;height:132px;background:linear-gradient(#fbb62a,var(--orange-mid) 80%,var(--orange-deep))}
.top-bar{left:0;top:0;width:1200px;height:11px;background:var(--bar-grey)}
.phone-box{left:809px;top:11px;width:214px;height:37px;background:var(--phone-grey);border-radius:0 0 4px 4px;display:flex;align-items:center;color:#fff}
.phone-box .icon{width:48px;height:100%;display:flex;align-items:center;justify-content:center;border-right:1px solid #234a73}
.phone-box .number{padding-left:12px;font-size:19px;white-space:nowrap}
.brand{left:175px;top:66px;font-size:21px;color:#3a2a14;white-space:nowrap}

.main-nav{left:441px;top:68px;width:582px;height:31px;display:flex;background:linear-gradient(var(--nav-blue),var(--nav-blue-dark));border-radius:3px;box-shadow:0 3px 4px rgba(0,0,0,.3);z-index:5}
.main-nav > a{flex:1;display:flex;align-items:center;justify-content:center;color:#fff;font-size:12px;text-decoration:none;border-right:1px solid var(--nav-divider-dark);border-left:1px solid var(--nav-divider-light)}
.main-nav > a:first-child{border-left:none}
.main-nav > a:last-child{border-right:none}
.main-nav > a.active{background:var(--nav-blue-dark)}
.dropdown{left:97px;top:31px;width:170px;background:#fff;border-top:3px solid var(--orange-deep);box-shadow:0 4px 8px rgba(0,0,0,.25);z-index:6}
.dropdown a{display:block;padding:0 14px;height:27px;line-height:27px;font-size:12px;color:var(--hero-blue);text-decoration:none;border-bottom:1px solid #e8edf2}
.dropdown a:last-child{border-bottom:none}

.hero{left:164px;top:143px;width:870px;height:396px;background:linear-gradient(#fff,#f4f4f4 55%,#e8e8e8);box-shadow:0 0 4px rgba(0,0,0,.25)}
.hero-shadow{left:168px;top:536px;width:862px;height:8px;background:radial-gradient(ellipse at center top,#111 0%,rgba(0,0,0,.6) 60%,transparent 72%)}
.showcase{left:52px;top:34px;width:340px;height:330px;display:flex;gap:10px}
.showcase figure{flex:1;position:relative;border:3px solid #fff;box-shadow:0 1px 4px rgba(0,0,0,.25)}
.showcase .before{background:linear-gradient(160deg,#a99b86,#7d6d58)}
.showcase .after{background:linear-gradient(160deg,#f0c890,#d9a060)}
.showcase figcaption{position:absolute;left:0;bottom:0;width:100%;height:26px;line-height:26px;text-align:center;font-size:13px;font-weight:700;color:#fff;letter-spacing:1px;text-transform:uppercase}
.showcase .before figcaption{background:rgba(40,40,40,.7)}
.showcase .after figcaption{background:rgba(29,79,135,.85)}
.hero-copy{left:410px;top:58px;width:420px;text-align:center}
.hero-copy h1{font-weight:400;font-size:23px;line-height:33px;color:var(--hero-blue)}
.hero-copy p{margin-top:12px;font-size:21px;color:#333}
.estimate-form{left:430px;top:206px;width:380px;background:#fff;border:1px solid var(--line);border-top:3px solid var(--orange-deep);padding:10px 14px 12px}
.estimate-form h3{font-size:14px;color:var(--heading-gold);font-weight:700;margin-bottom:8px}
.estimate-form .row{display:flex;gap:8px;margin-bottom:8px}
.estimate-form .row:last-child{margin-bottom:0}
.estimate-form input{flex:1;min-width:0;height:26px;border:1px solid var(--field-border);padding:0 8px;font:12px "PT Sans",Arial,sans-serif;color:#555;background:#fafcfe}
.estimate-form button{width:110px;height:26px;border:none;border-radius:2px;background:linear-gradient(var(--button-blue),var(--button-blue-dark));color:#fff;font:700 12px "PT Sans",Arial,sans-serif}
.arrow{top:173px;width:35px;height:33px;background:#e4e4e4;display:flex;align-items:center;justify-content:center}
.arrow.prev{left:0}.arrow.next{right:0}
.dots{left:746px;top:367px;display:flex;gap:4px}
.dots span{width:16px;height:16px;border-radius:50%;background:#d6d6d6;border:1px solid #c4c4c4}
.dots span.on{background:radial-gradient(circle,var(--hero-blue) 35%,#d6d6d6 40%)}

.panel{background:#fff;border:1px solid var(--line)}
.panel h2{font-weight:400;font-size:19px;color:var(--heading-gold)}
.panel p{font-size:11.5px;line-height:20px}
.welcome{left:166px;top:561px;width:868px;height:183px}
.welcome h2{position:absolute;left:19px;top:12px}
.welcome .rule{left:10px;top:42px;width:846px;height:1px;background:var(--line)}
.welcome p{position:absolute;left:19px;top:61px;width:596px}
.welcome .photo{left:631px;top:58px;width:223px;height:110px;background:linear-gradient(90deg,#3a3d42,#c9b8a8 55%,#e9e4de)}

.card{top:755px;width:416px;height:216px;box-shadow:0 2px 6px rgba(0,0,0,.18)}
.card h2{position:absolute;left:11px;top:12px}
.card .rule{left:0;top:44px;width:406px;height:1px;background:var(--line)}
.card.what{left:165px}
.card.guarantee{left:618px}
.card.guarantee h2{left:19px}
.card.guarantee .rule{left:10px}
.what .photo{left:14px;top:66px;width:149px;height:127px;background:linear-gradient(135deg,#d8d6d2,#8a7a6c 50%,#e9ebee)}
.what p{position:absolute;left:178px;top:63px;width:222px;line-height:18.5px}
.guarantee .seal{left:17px;top:62px}
.guarantee p{position:absolute;left:139px;top:59px;width:256px;line-height:18.5px}
.btn{width:77px;height:25px;background:linear-gradient(var(--button-blue),var(--button-blue-dark));color:#fff;font-size:12px;display:flex;align-items:center;justify-content:center;border-radius:2px}
.what .btn{left:179px;top:180px}
.guarantee .btn{left:140px;top:180px}

.site-footer{left:0;top:995px;width:1200px;height:121px;background:linear-gradient(var(--orange-mid),#fbb630)}
.footer-links{left:190px;top:17px;width:820px;text-align:center;font-size:11px;line-height:18.5px;color:var(--footer-link)}
.footer-links .sep{margin:0 8px;color:#a0340a}
.footer-rule{left:172px;top:82px;width:872px;height:1px;background:#d88a08}
.copyright{left:0;top:94px;width:1200px;text-align:center;font-size:11px;color:#6a1a05}
</style>
</head>
<body>
<header class="site-header abs">
  <div class="top-bar abs"></div>
  <div class="phone-box abs">
    <span class="icon"><svg width="18" height="14" viewBox="0 0 18 14"><path d="M1 4c0-3 16-3 16 0v2h-4V4.5H5V6H1z" fill="#fff"/><path d="M4 7h10l2 6H2z" fill="#fff"/><circle cx="9" cy="10" r="1.8" fill="#2f5f93"/></svg></span>
    <span class="number">1-800-555-0147</span>
  </div>
  <div class="brand abs">The Bramblewick Company</div>
  <nav class="main-nav abs">
    <a href="#">Home</a><a href="#" class="active">Residential ▾</a><a href="#">Commercial</a><a href="#">Fabrics</a><a href="#">About Us</a><a href="#">Contact Us</a>
    <div class="dropdown abs">
      <a href="#">Patio Furniture Repair</a>
      <a href="#">Pool Furniture Restrapping</a>
      <a href="#">Sling Replacement</a>
      <a href="#">Powdercoating</a>
    </div>
  </nav>
</header>

<section class="hero abs">
  <div class="showcase abs">
    <figure class="before" role="img" aria-label="Worn patio chair before refinishing"><figcaption>Before</figcaption></figure>
    <figure class="after" role="img" aria-label="Same patio chair after refinishing"><figcaption>After</figcaption></figure>
  </div>
  <div class="hero-copy abs">
    <h1>Welcome To The Bramblewick Company!<br>Patio Furniture Repair</h1>
    <p>DON’T REPLACE….RECYCLE !</p>
  </div>
  <form class="estimate-form abs">
    <h3>Request a Free Estimate</h3>
    <div class="row"><input type="text" placeholder="Name"><input type="text" placeholder="Phone"></div>
    <div class="row"><input type="text" placeholder="Email"><button type="button">Send Request</button></div>
  </form>
  <div class="arrow prev abs"><svg width="10" height="14"><path d="M8 1 2 7l6 6" stroke="#222" stroke-width="2.4" fill="none"/></svg></div>
  <div class="arrow next abs"><svg width="10" height="14"><path d="M2 1l6 6-6 6" stroke="#222" stroke-width="2.4" fill="none"/></svg></div>
  <div class="dots abs"><span></span><span></span><span class="on"></span><span></span><span></span><span></span></div>
</section>
<div class="hero-shadow abs"></div>

<section class="panel welcome abs">
  <h2>Welcome to our site</h2>
  <div class="rule abs"></div>
  <p>The Bramblewick Company has been refinishing patio furniture&nbsp; in the Mid-Atlantic Region since 1985.&nbsp; We have helped thousands of homeowners save considerably by restoring&nbsp; rather than replacing. We specialize in refinishing the types of high-end pool and Patio furniture which was originally built to last for generations.&nbsp; It is difficult, if not impossible, to purchase comparable quality anywhere ...... at any price. Please visit our other pages above to learn more detail of our outdoor furniture repair services or call now to receive a free estimate.</p>
  <div class="photo abs" role="img" aria-label="Client shaking hands with a company representative"></div>
</section>

<section class="panel card what abs">
  <h2>What we do</h2>
  <div class="rule abs"></div>
  <div class="photo abs" role="img" aria-label="Consultant meeting with homeowners"></div>
  <p>Wrought Iron Refinishing Custom Patio Furniture Sling Replacement Pool Furniture Restrapping Larkmoor Chair Relacing Powdercoating Patio Table Repair Cast Aluminum Repainting Advice on Care and Cleaning Free Estimates...</p>
  <div class="btn abs">Read More&gt;&gt;</div>
</section>

<section class="panel card guarantee abs">
  <h2>Guarantee</h2>
  <div class="rule abs"></div>
  <svg class="seal abs" width="100" height="100" viewBox="0 0 100 100" role="img" aria-label="Satisfaction guarantee seal">
    <circle cx="50" cy="50" r="48" fill="#e2a812"/>
    <circle cx="50" cy="50" r="38" fill="#f6cf3a" stroke="#b27c06" stroke-width="2"/>
    <circle cx="50" cy="50" r="20" fill="#e9b51d"/>
  </svg>
  <p>When someone chooses The Bramblewick Company, they are assured a professional service and product.&nbsp; Every piece of furniture that leaves our warehouse is 100% guaranteed.&nbsp; As part of the refurbishing process, you will be given instructions on how to care for your newly .</p>
  <div class="btn abs">Read More&gt;&gt;</div>
</section>

<footer class="site-footer abs">
  <div class="footer-links abs">
    Patio Furniture Repair<span class="sep">|</span>Larkmoor Repair<span class="sep">|</span>Repair Patio Chair<span class="sep">|</span>Garden Patio Furniture Replacement<span class="sep">|</span>Larkmoor Furniture Repair<span class="sep">|</span>Outdoor Furniture<br>Refinish<span class="sep">|</span>Patio Furniture Refurbishing<span class="sep">|</span>Cleaning &amp; Care of Pool&nbsp; Furniture<span class="sep">|</span>Patio Chair Repair<span class="sep">|</span>Patio Furniture Refurbishing Article<span class="sep">|</span><br>Garden Patio Furniture Replacement Article<span class="sep">|</span>Sitemap
  </div>
  <div class="footer-rule abs"></div>
  <div class="copyright abs">Copyrights @ 2012&nbsp; All Rights Reserved</div>
</footer>
</body>
</html>
```